Judicial election website to attract voters

I need a simple one-page web design for a judicial election. I'm going to put up one picture, maybe two. The picture I have needs a little touch-up (whiten teeth for example). I have 3 paragraphs of text. I'd like a "Donate" button that can link to a CoinDrift account. I'd also like a little background design, like the Constitution or something like that. There's a couple other little things but that's the bulk of it.

Target Market(s)

Involved voters and some media

Industry/Entity Type

Legal

Number of Pages Required

1 page

Font styles to use
Sans Serif

Requirements
Must have
• My picture, text, donate button
• Phrase "Remember to vote August 30, 2016!"
Nice to have
• Perhaps a second photo, maybe a short 30 second video of me talking directly to the voters, cool background: Constitution, something judgey.
Should not have
• Not sure ... profanity, I guess.

```html
<!DOCTYPE html>
<html lang="en">
<head>
<meta charset="utf-8">
<title>Hometown Vote – Remember to Vote</title>
<link rel="stylesheet" href="https://fonts.googleapis.com/css2?family=Lato:wght@400;700;900&family=Tenor+Sans&display=swap">
<style>
  :root {
    --navy: #15306f;
    --navy-deep: #0f2a66;
    --red: #b5202f;
    --red-bright: #c8262f;
    --sky: #8ec3e6;
    --mist: #e6eef4;
    --ink: #111111;
    --white: #ffffff;
  }
  * { box-sizing: border-box; margin: 0; padding: 0; }
  html, body { width: 912px; height: 1200px; overflow: hidden; }
  body { font-family: "Lato", sans-serif; color: var(--ink); background: var(--white); }
  .page { position: relative; width: 912px; height: 1200px; overflow: hidden; }

  .hero {
    position: absolute; left: 0; top: 0; width: 912px; height: 396px;
    background: linear-gradient(160deg, #2b4d8f 0%, #a8303f 30%, #c75a66 48%, #e7d6da 66%, #a9cfe9 88%, var(--sky) 100%);
  }
  .brand {
    position: absolute; left: 77px; top: 27px;
    display: flex; align-items: center; gap: 12px;
  }
  .brand-dot { width: 30px; height: 30px; border-radius: 50%; background: var(--red-bright); }
  .brand-name {
    font-family: "Tenor Sans", sans-serif; font-size: 25px; line-height: 30px;
    color: var(--white); letter-spacing: 0.5px;
  }
  .donate {
    position: absolute; left: 695px; top: 32px; height: 31px;
    display: flex; align-items: center;
    background: var(--navy-deep); color: var(--white);
    font-size: 14px; font-weight: 700; letter-spacing: 0.3px;
    padding-right: 9px; border-radius: 3px 0 0 3px;
  }
  .donate-icon {
    width: 35px; height: 35px; border-radius: 50%; background: var(--white);
    border: 3px solid var(--navy-deep); margin: 0 10px 0 -2px;
  }
  .vote-band {
    position: absolute; left: 0; top: 251px; width: 912px; height: 90px;
    background: rgba(255,255,255,0.5); text-align: center;
  }
  .vote-band .lead { margin-top: 6px; font-size: 26px; font-weight: 700; color: var(--navy); line-height: 32px; }
  .vote-band .date { font-size: 33px; font-weight: 700; color: var(--red); line-height: 42px; }
  .slider-dots { position: absolute; left: 436px; top: 356px; display: flex; gap: 6px; }
  .slider-dots span { width: 9px; height: 9px; border-radius: 50%; background: var(--white); }
  .slider-dots .active { background: var(--red); border: 2px solid var(--white); }

  .about {
    position: absolute; left: 0; top: 396px; width: 912px; height: 346px;
    background: linear-gradient(180deg, #f4f7fa 0%, var(--mist) 55%, #c9d4cf 100%);
  }
  .portrait-frame {
    position: absolute; left: 75px; top: 65px; width: 296px; height: 234px;
    background: #4b3a22; padding: 12px;
    border: 3px solid #2b1e0e;
  }
  .portrait {
    width: 100%; height: 100%; background: linear-gradient(160deg, #e9e4df, #cdb4a6);
    border: 3px solid var(--white); outline: 1px solid #333; outline-offset: -6px;
  }
  .bio { position: absolute; left: 403px; top: 71px; width: 424px; }
  .bio p { font-size: 11.8px; font-weight: 700; line-height: 16.8px; margin-bottom: 9.6px; }

  .video {
    position: absolute; left: 0; top: 742px; width: 912px; height: 422px;
    background: linear-gradient(180deg, #163576 0%, var(--navy) 60%, #1b3d84 100%);
  }
  .video h2 {
    position: absolute; left: 0; top: 70px; width: 912px; text-align: center;
    font-family: "Tenor Sans", sans-serif; font-weight: 400; font-size: 25px; color: var(--white);
    -webkit-text-stroke: 0.4px var(--white);
  }
  .video-player {
    position: absolute; left: 296px; top: 126px; width: 330px; height: 296px;
    background: linear-gradient(135deg, #d9d9df 0%, #b23a48 50%, #e8e8ee 100%);
    border-radius: 10px 10px 0 0;
  }
  .play {
    position: absolute; left: 141px; top: 90px; width: 50px; height: 50px; border-radius: 50%;
    background: rgba(255,255,255,0.9);
  }
  .chevron { position: absolute; left: 432px; }

  .footer {
    position: absolute; left: 0; top: 1164px; width: 912px; height: 36px;
    background: var(--red); color: var(--white);
    font-size: 10px; font-weight: 700; text-align: center; line-height: 36px;
  }
</style>
</head>
<body>
<div class="page">
  <header class="hero" role="img" aria-label="Waving national flag against a blue sky">
    <div class="brand"><span class="brand-dot"></span><span class="brand-name">HOMETOWN VOTE</span></div>
    <a class="donate"><span class="donate-icon"></span>DONATE NOW</a>
    <div class="vote-band">
      <p class="lead">Remember to vote</p>
      <p class="date">August 30, 2016!</p>
    </div>
    <div class="slider-dots"><span></span><span class="active"></span><span></span></div>
  </header>

  <section class="about" role="img" aria-label="Faded view of a white government building behind trees">
    <div class="portrait-frame">
      <div class="portrait" role="img" aria-label="Portrait photo of the candidate"></div>
    </div>
    <div class="bio">
      <p>Lorem ipsum dolor sit amet, consectetuer adipiscing elit, sed diam nonummy nibher euismod tincidunt ut laoreet dolore magna aliquam erat volutpat. Ut wisi enim ader minim veniam, quis nostrud exerci tation ullamcorper suscipit lobortis nisl ut ewrwi aliquip ex ea commodo consequat.</p>
      <p>Lorem ipsum dolor sit amet, consectetuer adipiscing elit, sed diam nonummy nibher euismod tincidunt ut laoreet dolore magna aliquam erat volutpat. Ut wisi enim ader minim veniam, quis nostrud exerci tation ullamcorper suscipit lobortis nisl ut ewrwi aliquip ex ea commodo consequat.</p>
      <p>Lorem ipsum dolor sit amet, consectetuer adipiscing elit, sed diam nonummy nibher euismod tincidunt ut laoreet dolore magna aliquam erat volutpat. Ut wisi enim ader minim veniam, quis nostrud exerci tation ullamcorper suscipit lobortis nisl ut ewrwi aliquip ex ea commodo consequat.</p>
    </div>
  </section>

  <svg class="chevron" style="top:390px" width="48" height="30" viewBox="0 0 48 30">
    <polygon points="0,6 48,6 24,30" fill="#9fcbe6"/>
    <polyline points="4,0 24,18 44,0" fill="none" stroke="#ffffff" stroke-width="2"/>
  </svg>

  <section class="video" role="img" aria-label="Navy background with courthouse columns">
    <h2>WATCH THE VIDEO</h2>
    <div class="video-player" role="img" aria-label="Hands holding a tablet showing a video of a ballot box and flag">
      <span class="play"></span>
    </div>
  </section>

  <svg class="chevron" style="top:742px" width="48" height="24" viewBox="0 0 48 24">
    <polygon points="0,0 48,0 24,24" fill="#eef2f3"/>
    <polyline points="8,0 24,14 40,0" fill="none" stroke="#111111" stroke-width="1.6"/>
  </svg>

  <footer class="footer">Copyright © 2016 Hometown Vote &nbsp;|&nbsp; All Rights Reserved</footer>
</div>
</body>
</html>
```